Webdesign für Bedrucken Papiertaschen, Schildern etc.
Zielgruppe
Wir bedrucken Papiertaschen, Papierbeutel, Laternen, Aluplaketten, Schilder, etc. und lasern Hundemarken. Zielgruppen von Privat bis Geschäftskunden
Aufgabenstellung
Der Shop sollte ein einfacher und kostengünstiger 'Druckfalter'-shop werden. Wo die Kunden anhand von einem Editor Ihre Logos oder Druckvorlagen selber hochladen und/oder gestalten könne. Bisher haben die Kunden eifach ihre Bidldatei per E-Mail geschickt und wir haben diese dann weiter verarbeit.
Der Shop sollte, wenn möglich, günstig im Unterhalt sein, da wir nicht abschätzen können, wie gut diese laufen wird.
Wir haben wie 3 Bereich: 1. Papierbeutel/Taschen / 2. Stallplaketten (für z.B. Pferdesport) / 3. Diverses (Wie z.B. die Laternen, Schilder, Hundemarken, etc.)
Es würde sich um eine separate Webseite handeln. Daher ist bei Design freie Hand, eifach und klar... auch für nicht so ambitionierte Privatkunden oder kleine Unternehmen.

```html
<!DOCTYPE html>
<html lang="de">
<head>
<meta charset="utf-8">
<title>Druckfalter – Druckprodukte online gestalten</title>
<link href="https://fonts.googleapis.com/css2?family=Inter+Tight:wght@500;600;700;800&family=Inter:wght@400;500;600;700&display=swap" rel="stylesheet">
<style>
:root{
  --stage:#c2c2c2;
  --paper:#ffffff;
  --ink:#0f1216;
  --ink-2:#2b2f36;
  --muted:#6b7078;
  --line:#ececec;
  --soft:#f4f5f3;
  --lime:#b9ef3b;
  --lime-soft:#eefbd0;
  --lime-text:#9ccf1e;
}
*{box-sizing:border-box;margin:0;padding:0}
html,body{width:1200px;height:2858px;overflow:hidden;background:var(--stage)}
body{font-family:Inter,sans-serif;color:var(--ink)}
.stage{width:1082px;height:2576px;transform:scale(1.10906);transform-origin:0 0;position:relative}
.page{position:absolute;left:83px;top:72px;width:917px;height:2440px;background:var(--paper);overflow:hidden}
.abs{position:absolute}
.h{font-family:"Inter Tight",sans-serif;font-weight:700;letter-spacing:-.03em}
.label{font-size:8px;font-weight:600;letter-spacing:.16em;text-transform:uppercase;color:var(--muted)}
.label.lime{color:var(--lime-text)}
.btn{display:inline-flex;align-items:center;gap:6px;border-radius:999px;font-size:10px;font-weight:600;height:30px;padding:0 16px}
.btn-dark{background:var(--ink);color:#fff}
.btn-lime{background:var(--lime);color:var(--ink)}
.card{background:#fff;border:1px solid var(--line);border-radius:14px}

/* nav */
.nav{left:77px;top:16px;width:758px;height:32px;border-radius:12px;background:#fff;box-shadow:0 2px 10px rgba(0,0,0,.06);display:flex;align-items:center;padding:0 0 0 13px}
.brand{font-family:"Inter Tight",sans-serif;font-weight:700;font-size:20px;letter-spacing:-.03em;display:flex;align-items:center;gap:6px}
.brand .dot{width:10px;height:10px;background:var(--lime);border-radius:2px}
.nav-links{margin-left:auto;display:flex;gap:20px;font-size:9.5px;color:var(--ink-2);margin-right:22px}
.nav .search{width:22px;height:22px;border-radius:50%;border:1px solid var(--line);display:grid;place-items:center;margin-right:7px}
.nav .btn{height:22px;font-size:9.5px;padding:0 13px}

/* hero */
.hero{left:82px;top:81px;width:433px;height:313px;border-radius:14px;background:var(--ink);color:#fff;padding:30px 30px;overflow:hidden;
  background-image:linear-gradient(rgba(255,255,255,.035) 1px,transparent 1px),linear-gradient(90deg,rgba(255,255,255,.035) 1px,transparent 1px);background-size:18px 18px}
.pill-dark{display:inline-flex;align-items:center;gap:5px;font-size:7.5px;background:rgba(255,255,255,.08);border-radius:999px;padding:4px 8px}
.pill-dark i{width:4px;height:4px;border-radius:50%;background:var(--lime)}
.hero h1{font-size:41px;line-height:42px;margin-top:12px}
.hero h1 .grey{color:#8d9097}
.hero h1 .mark{display:inline-block;background:var(--lime);color:var(--ink);padding:0 7px;border-radius:8px;line-height:44px}
.hero p{font-size:10.5px;line-height:17px;color:#c9ccd1;margin-top:16px;width:360px}
.hero .actions{display:flex;gap:8px;margin-top:18px}
.btn-ghost{border:1px solid #2f343b;color:#fff}
.btn .arrow{width:14px;height:14px;border-radius:50%;background:var(--ink);display:grid;place-items:center}

.stat{top:81px;width:144px;height:135px;border-radius:14px;padding:15px 15px}
.stat.rate{left:530px;border:1px solid var(--line)}
.stat.check{left:690px;background:var(--lime)}
.stat .big{font-family:"Inter Tight",sans-serif;font-weight:700;font-size:20px;margin-top:4px}
.stat small{font-size:7.5px;color:var(--muted);display:block;line-height:10px}
.stat.check small{color:var(--ink-2)}
.stat.check .label{color:#5e7d10}
.tools{left:530px;top:231px;width:304px;height:163px;padding:15px 14px}
.chips{display:flex;flex-wrap:wrap;gap:5px;margin-top:10px;width:270px}
.chip{display:inline-flex;align-items:center;gap:4px;font-size:8px;border:1px solid var(--line);border-radius:999px;padding:4px 8px}
.tools .link{font-size:9px;color:var(--lime-text);margin-top:14px;display:block}

/* section heads */
.sec-h{font-size:22px}
.more{font-size:9.5px;font-weight:600}

/* products */
.prod{top:510px;width:242px;height:308px;overflow:hidden}
.prod .img{height:182px;position:relative}
.prod .tag{position:absolute;left:10px;top:10px;background:#fff;border-radius:999px;font-size:7.5px;font-weight:500;padding:3px 7px}
.prod .body{padding:17px 15px}
.prod h3{font-size:15px;line-height:18px;letter-spacing:-.02em}
.prod p{font-size:8.5px;color:var(--muted);line-height:13px;margin-top:9px}
.prod .foot{display:flex;justify-content:space-between;align-items:center;margin-top:12px;font-size:9px;font-weight:600}
.go{width:22px;height:22px;border-radius:50%;background:var(--soft);display:grid;place-items:center}

/* steps */
.steps{left:82px;top:883px;width:752px;height:223px;padding:26px 24px}
.steps .intro{position:absolute;right:28px;top:42px;width:250px;font-size:9px;color:var(--muted);line-height:14px}
.step-row{display:flex;margin-top:28px}
.step{width:179px;position:relative}
.step .num{width:42px;height:42px;border-radius:50%;border:1px solid var(--line);display:grid;place-items:center;font-family:"Inter Tight",sans-serif;font-weight:700;font-size:13px;background:#fff;position:relative;z-index:1}
.step .rule{position:absolute;left:42px;top:21px;width:137px;height:1px;background:var(--line)}
.step h4{font-size:11px;margin-top:17px;font-weight:600}
.step p{font-size:8.5px;color:var(--muted);line-height:14px;margin-top:8px;width:150px}
.done{position:absolute;left:50px;top:14px;background:var(--lime);font-size:6.5px;font-weight:700;border-radius:999px;padding:3px 6px;z-index:1}

/* editor */
.editor{left:82px;top:1250px;width:752px;height:483px;overflow:hidden;display:flex}
.ed-left{width:159px;border-right:1px solid var(--line);padding:9px 10px}
.add-grid{display:grid;grid-template-columns:1fr 1fr;gap:5px;margin-top:7px}
.add{height:38px;border:1px solid var(--line);border-radius:6px;display:flex;flex-direction:column;align-items:center;justify-content:center;gap:3px;font-size:7.5px;font-weight:500}
.add.on{background:var(--lime);border-color:var(--lime)}
.hr{height:1px;background:var(--line);margin:9px -10px}
.swatches{display:flex;gap:5px;margin-top:8px}
.sw{width:16px;height:16px;border-radius:50%}
.layer{display:flex;align-items:center;gap:8px;font-size:8px;height:20px;padding:0 6px;border-radius:5px;margin-top:3px}
.layer.on{background:var(--lime-soft);border:1px solid #d9f39c}
.layer b{font-family:serif;font-weight:400;color:var(--muted);width:8px}
.ed-mid{flex:1;background:#f3f4f2;position:relative}
.ed-bar{height:32px;background:#fff;border-bottom:1px solid var(--line);display:flex;align-items:center;padding:0 10px;gap:8px;font-size:8px}
.seg{display:flex;background:var(--soft);border-radius:6px;padding:2px}
.seg span{padding:4px 8px;border-radius:5px;color:var(--muted)}
.seg span.on{background:#fff;color:var(--ink);font-weight:600}
.tb-green{background:var(--lime-soft);border-radius:5px;padding:4px 7px;font-weight:500}
.tb-dark{background:var(--ink);color:#fff;border-radius:5px;padding:4px 8px}
.art-cap{position:absolute;left:107px;top:99px;font-size:6.5px;color:var(--muted)}
.art{position:absolute;left:107px;top:111px;width:207px;height:292px;background:#fff;box-shadow:0 2px 8px rgba(0,0,0,.08)}
.art .bleed{position:absolute;inset:9px;border:1px solid #eef5d9}
.art .name{position:absolute;left:19px;top:56px;font-size:8px;font-weight:700;letter-spacing:.04em}
.art .circle{position:absolute;left:92px;top:38px;width:58px;height:58px;border-radius:50%;background:var(--lime)}
.art .sel{position:absolute;left:-22px;top:173px;width:147px;height:34px;border:1.5px solid var(--ink);text-align:center;font-family:"Inter Tight",sans-serif;font-weight:600;font-size:13px;line-height:14px;padding-top:3px}
.sel i{position:absolute;width:5px;height:5px;background:#fff;border:1.5px solid var(--ink);border-radius:50%}
.art .small{position:absolute;left:-12px;top:253px;font-size:5px;color:var(--muted)}
.live{position:absolute;left:10px;bottom:10px;background:#fff;border-radius:999px;font-size:7px;padding:4px 8px;display:flex;gap:4px;align-items:center}
.live i{width:4px;height:4px;border-radius:50%;background:var(--lime)}
.ed-right{width:171px;border-left:1px solid var(--line);padding:10px 10px}
.field-l{font-size:6.5px;font-weight:600;letter-spacing:.12em;color:var(--muted);margin-top:15px;margin-bottom:5px}
.field{border:1px solid var(--line);border-radius:6px;font-size:8px;padding:6px 7px}
.two{display:grid;grid-template-columns:1fr 1fr;gap:5px}
.align{display:flex;border:1px solid var(--line);border-radius:6px;height:20px}
.align span{flex:1;display:grid;place-items:center;font-size:8px;color:var(--muted)}
.align span.on{background:var(--soft)}
.colors{display:flex;gap:5px;flex-wrap:wrap}
.colors i{width:15px;height:15px;border-radius:50%}

/* features */
.feat{top:1813px;width:243px;height:113px;padding:16px 15px}
.feat .ic{width:27px;height:27px;border-radius:7px;background:var(--ink);display:grid;place-items:center}
.feat h4{font-size:11px;margin-top:16px;font-weight:600}
.feat p{font-size:8.5px;color:var(--muted);line-height:13px;margin-top:7px}

/* cta */
.cta{left:82px;top:1966px;width:752px;height:139px;background:var(--lime);border-radius:14px}
.cta h2{position:absolute;left:43px;top:42px;font-size:32px;line-height:34px}
.cta .acts{position:absolute;right:43px;top:55px;display:flex;gap:8px}
.btn-line{border:1px solid rgba(15,18,22,.25);color:var(--ink)}

/* footer */
.footer{left:0;top:2183px;width:917px;height:257px;background:var(--ink);color:#fff}
.footer .brand{position:absolute;left:82px;top:36px;color:#fff}
.footer .about{position:absolute;left:82px;top:74px;width:240px;font-size:9px;line-height:13px;color:#a3a7ad}
.footer .btn{position:absolute;left:82px;top:122px;height:24px;font-size:9.5px}
.fcol{position:absolute;top:40px;font-size:9px}
.fcol h5{font-size:9px;font-weight:600;margin-bottom:14px}
.fcol a{display:block;color:#a3a7ad;margin-bottom:10px;text-decoration:none}
.fcol .ct{display:flex;gap:7px;color:#c5c8cc;margin-bottom:9px;line-height:12px}
.fbottom{position:absolute;left:82px;right:86px;top:234px;display:flex;font-size:7.5px;color:#7c8088}
.fbottom span{margin-left:auto;display:flex;gap:18px}
</style>
</head>
<body>
<div class="stage">
<div class="page">

  <nav class="nav abs">
    <div class="brand">Druckfalter<span class="dot"></span></div>
    <div class="nav-links"><span>Produkte</span><span>Editor</span><span>Beispiel</span><span>Kontakt</span></div>
    <div class="search"><svg width="10" height="10" viewBox="0 0 10 10"><circle cx="4.3" cy="4.3" r="3.2" fill="none" stroke="#0f1216" stroke-width="1.1"/><path d="M6.7 6.7L9 9" stroke="#0f1216" stroke-width="1.1"/></svg></div>
    <a class="btn btn-dark">Editor öffnen <svg width="7" height="7" viewBox="0 0 8 8"><path d="M2 6L6 2M3 2h3v3" stroke="#fff" fill="none" stroke-width="1.2"/></svg></a>
  </nav>

  <section class="hero abs">
    <span class="pill-dark"><i></i>Neuer Druckfalter-Editor · v2.4</span>
    <h1 class="h">Druckprodukte.<br><span class="grey">Online gestalten.</span><br><span class="mark">Ohne E-Mail.</span></h1>
    <p>Logo hochladen, Text setzen, Vorder- und Rückseite prüfen — und absenden. Wir prüfen jede Datei persönlich vor dem Druck.</p>
    <div class="actions">
      <a class="btn btn-lime">Editor öffnen <span class="arrow"><svg width="7" height="7" viewBox="0 0 8 8"><path d="M2 6L6 2M3 2h3v3" stroke="#fff" fill="none" stroke-width="1.2"/></svg></span></a>
      <a class="btn btn-ghost"><svg width="10" height="10" viewBox="0 0 10 10"><path d="M5 7V1M2.5 3.5L5 1l2.5 2.5M1 7v2h8V7" stroke="#fff" fill="none" stroke-width="1"/></svg>Datei hochladen</a>
    </div>
  </section>

  <div class="stat rate abs">
    <div class="label">Bewertung</div>
    <div style="margin-top:50px;font-size:10px;letter-spacing:1px">★★★★★</div>
    <div class="big" style="margin-top:0">4,9</div>
    <small>von 380 Kunden</small>
  </div>
  <div class="stat check abs">
    <div class="label">Prüfung</div>
    <div class="big" style="margin-top:58px">100%</div>
    <small>der Druckdaten persönlich geprüft, bevor produziert wird.</small>
  </div>

  <div class="card tools abs">
    <div class="label">Im Editor verfügbar</div>
    <div class="chips">
      <span class="chip">T&nbsp;Text</span><span class="chip">▣ Logo Upload</span><span class="chip">▢ Formen</span><span class="chip">◎ Farben</span><span class="chip">➚ Drag &amp; Drop</span><span class="chip">✦ Vorlagen</span>
    </div>
    <span class="link">Editor live ausprobieren →</span>
  </div>

  <div class="abs label lime" style="left:82px;top:445px">01 — Produkte</div>
  <h2 class="abs h sec-h" style="left:82px;top:461px">Was möchten Sie drucken?</h2>
  <div class="abs more" style="left:767px;top:474px">Alle Produkte →</div>

  <article class="card prod abs" style="left:82px">
    <div class="img" role="img" aria-label="Illustration einer gelben Papiertasche mit Markenlogo" style="background:linear-gradient(160deg,#fff0c2,#fde3a6 60%,#fcd9a0)"><span class="tag">Verpackung</span></div>
    <div class="body"><h3 class="h">Papierbeutel<br>&amp; Taschen</h3><p>Standbodenbeutel, Tragetaschen, mit oder ohne Fenster.</p>
    <div class="foot">ab CHF 1.20<span class="go">↗</span></div></div>
  </article>
  <article class="card prod abs" style="left:337px">
    <div class="img" role="img" aria-label="Illustration einer rosa ovalen Stallplakette" style="background:linear-gradient(160deg,#fde2e6,#fbd0dc 60%,#f7cde8)"><span class="tag">Pferdesport</span></div>
    <div class="body"><h3 class="h">Stallplaketten<br>&amp; Schilder</h3><p>Holz, Aluminium, oval oder eckig — mit Wunschtext.</p>
    <div class="foot">ab CHF 24.00<span class="go">↗</span></div></div>
  </article>
  <article class="card prod abs" style="left:592px">
    <div class="img" role="img" aria-label="Illustration von Laterne und Hundemarke in Lila" style="background:linear-gradient(160deg,#ecebfd,#d9dcfb 60%,#cfd4f7)"><span class="tag">Diverses</span></div>
    <div class="body"><h3 class="h">Laternen, Marken<br>&amp; mehr</h3><p>Personalisierte Laser- und Druckprodukte.</p>
    <div class="foot">ab CHF 14.90<span class="go">↗</span></div></div>
  </article>

  <section class="card steps abs">
    <div class="label lime">02 — Ablauf</div>
    <h2 class="h sec-h" style="margin-top:6px">In 4 Schritten zur Druckdatei.</h2>
    <p class="intro">Vom Produkt zur fertigen Druckdatei — geführt, geprüft, ohne Umwege.</p>
    <div class="step-row">
      <div class="step"><span class="rule"></span><div class="num">01</div><h4>Produkt wählen</h4><p>Aus dem Katalog auswählen und Variante festlegen.</p></div>
      <div class="step"><span class="rule"></span><div class="num">02</div><h4>Gestalten oder hochladen</h4><p>Editor öffnen oder fertige Druckdatei hochladen.</p></div>
      <div class="step"><span class="rule"></span><div class="num">03</div><h4>Vorder- + Rückseite prüfen</h4><p>Beide Seiten separat kontrollieren in der Vorschau.</p></div>
      <div class="step"><span class="rule"></span><div class="num">04</div><span class="done">FERTIG</span><h4>Absenden &amp; geniessen</h4><p>Wir prüfen die Daten persönlich und drucken.</p></div>
    </div>
  </section>

  <div class="abs label lime" style="left:82px;top:1167px">03 — Editor</div>
  <h2 class="abs h sec-h" style="left:82px;top:1183px">Direkt im Browser gestalten.</h2>
  <p class="abs" style="left:82px;top:1217px;font-size:10px;color:var(--muted)">Kein Mockup — das ist der echte Editor. Probier ihn gleich hier aus.</p>
  <a class="abs btn btn-dark" style="left:732px;top:1201px;height:28px;font-size:9.5px">Vollbild öffnen ↗</a>

  <section class="card editor abs">
    <aside class="ed-left">
      <div class="field-l" style="margin-top:0">HINZUFÜGEN</div>
      <div class="add-grid">
        <div class="add"><span style="font-size:11px">T</span>Text</div>
        <div class="add"><span>▣</span>Bild</div>
        <div class="add"><span>▢</span>Form</div>
        <div class="add on"><span>⤒</span>Upload</div>
      </div>
      <div class="hr"></div>
      <div class="field-l" style="margin-top:0">HINTERGRUND</div>
      <div class="swatches">
        <i class="sw" style="border:2px solid var(--lime);background:#fff"></i><i class="sw" style="background:#f6e6d6"></i><i class="sw" style="background:#0f1216"></i><i class="sw" style="background:#fdf0c4"></i><i class="sw" style="background:#dde7fb"></i>
      </div>
      <div class="hr"></div>
      <div class="field-l" style="margin-top:0">◈ EBENEN (4)</div>
      <div class="layer"><b>T</b>1.2 kg · natürlich · sch…</div>
      <div class="layer on"><b>T</b>Premium</div>
      <div class="layer"><b>▢</b>Form</div>
      <div class="layer"><b>T</b>WALDKORN</div>
    </aside>
    <div class="ed-mid">
      <div class="ed-bar">
        <div class="seg"><span class="on">Vorderseite</span><span>Rückseite</span></div>
        <span style="color:var(--muted);margin-left:8px">↶</span><span style="color:var(--muted)">↷</span>
        <span class="tb-green">▦ Hilfslinien</span>
        <span style="margin-left:auto;color:var(--muted)">⊖</span><span>100%</span><span style="color:var(--muted)">⊕</span>
        <span class="tb-dark">Vorschau</span>
      </div>
      <div class="art-cap">210 × 297 mm · 3 mm Beschnitt</div>
      <div class="art">
        <div class="bleed"></div>
        <div class="name">WALDKORN</div>
        <div class="circle"></div>
        <div class="sel">Premium<br>Hauptfutter<i style="left:-3px;top:-3px"></i><i style="right:-3px;top:-3px"></i><i style="left:-3px;bottom:-3px"></i><i style="right:-3px;bottom:-3px"></i></div>
        <div class="small">1.2 kg · natürlich · schweizer herkunft</div>
      </div>
      <div class="live"><i></i>Live · Vorderseite · Druckbereich sichtbar</div>
    </div>
    <aside class="ed-right">
      <div style="display:flex;justify-content:space-between;font-size:8.5px;font-weight:600;letter-spacing:.1em">TEXT<span style="color:var(--muted);letter-spacing:0">⧉ <span style="color:#e04848">🗑</span></span></div>
      <div class="field-l" style="margin-top:26px">TEXT</div>
      <div class="field" style="height:42px">Premium<br>Hauptfutter</div>
      <div class="field-l">SCHRIFT</div>
      <div class="field" style="display:flex;justify-content:space-between">Space Grotesk<span>⌄</span></div>
      <div class="two"><div class="field-l">GRÖSSE</div><div class="field-l">GEWICHT</div></div>
      <div class="two"><div class="field">22</div><div class="field">Bold</div></div>
      <div class="field-l">AUSRICHTUNG</div>
      <div class="align"><span>≡</span><span class="on">≡</span><span>≡</span></div>
      <div class="field-l">STIL</div>
      <div style="display:flex;gap:4px"><span style="width:19px;height:19px;border-radius:50%;background:var(--lime-soft);display:grid;place-items:center;font-size:8px;font-weight:700;color:var(--lime-text)">B</span><span style="width:19px;height:19px;border-radius:50%;border:1px solid var(--line);display:grid;place-items:center;font-size:8px;font-style:italic">I</span></div>
      <div class="field-l">FARBE</div>
      <div class="colors">
        <i style="background:#0f1216;box-shadow:0 0 0 2px #fff,0 0 0 3px var(--lime)"></i><i style="background:#6f6cf2"></i><i style="background:#2fc46c"></i><i style="background:#ef4444"></i><i style="background:#f59e0b"></i><i style="background:#ec4fa0"></i><i style="background:#1fa6e8"></i><i style="background:#fff;border:1px solid var(--line)"></i><i style="border:1px solid var(--line);font-size:7px;font-style:normal;display:grid;place-items:center">◎</i>
      </div>
      <div class="two"><div class="field-l">X (%)</div><div class="field-l">Y (%)</div></div>
      <div class="two"><div class="field">60</div><div class="field">70</div></div>
      <div class="two"><div class="field-l" style="margin-top:10px">BREITE (%)</div><div class="field-l" style="margin-top:10px">ROTATION</div></div>
      <div class="two"><div class="field">70</div><div class="field">↻ &nbsp;0</div></div>
    </aside>
  </section>

  <div class="card feat abs" style="left:82px">
    <div class="ic"><svg width="12" height="12" viewBox="0 0 12 12"><path d="M6 1l4 1.5V6c0 2.4-1.8 4.2-4 5-2.2-.8-4-2.6-4-5V2.5z" fill="none" stroke="#b9ef3b" stroke-width="1"/><path d="M4.2 6l1.3 1.3L8 4.8" stroke="#b9ef3b" fill="none" stroke-width="1"/></svg></div>
    <h4>Persönliche Datenprüfung</h4><p>Jede Druckdatei wird vor dem Druck geprüft — keine bösen Überraschungen.</p>
  </div>
  <div class="card feat abs" style="left:337px">
    <div class="ic"><svg width="12" height="12" viewBox="0 0 10 10"><path d="M5 7V1M2.5 3.5L5 1l2.5 2.5M1 7v2h8V7" stroke="#b9ef3b" fill="none" stroke-width="1"/></svg></div>
    <h4>Upload als Alternative</h4><p>Fertige Datei? Direkt hochladen. Kein Editor-Zwang.</p>
  </div>
  <div class="card feat abs" style="left:591px">
    <div class="ic"><svg width="12" height="12" viewBox="0 0 12 12"><path d="M6 1.5l1 3 3 1-3 1-1 3-1-3-3-1 3-1z" fill="#b9ef3b"/></svg></div>
    <h4>Schweizer Druckpartner</h4><p>Lokale Produktion, geprüfte Materialien, faire Preise.</p>
  </div>

  <section class="cta abs">
    <h2 class="h">Bereit, dein Produkt zu<br>gestalten?</h2>
    <div class="acts"><a class="btn btn-dark">Editor öffnen ↗</a><a class="btn btn-line">Produkte ansehen</a></div>
  </section>

  <footer class="footer abs">
    <div class="brand">Druckfalter<span class="dot"></span></div>
    <p class="about">Druckprodukte online gestalten — Editor, Upload und persönliche Datenprüfung. Lokale Produktion in der Schweiz.</p>
    <a class="btn btn-lime">Editor öffnen ↗</a>
    <div class="fcol" style="left:394px"><h5>Produkte</h5><a>Papierbeutel</a><a>Stallplaketten</a><a>Laternen</a><a>Hundemarken</a><a>Alle Produkte</a></div>
    <div class="fcol" style="left:499px"><h5>Service</h5><a>Editor öffnen</a><a>Datei hochladen</a><a>Datenprüfung</a><a>Versand</a><a>Kontakt</a></div>
    <div class="fcol" style="left:604px"><h5>Unternehmen</h5><a>Über uns</a><a>Druckpartner</a><a>Nachhaltigkeit</a><a>Impressum</a><a>Datenschutz</a></div>
    <div class="fcol" style="left:720px"><h5>Kontakt</h5>
      <div class="ct"><span style="color:var(--lime)">✉</span>hallo@druckfalter.ch</div>
      <div class="ct"><span style="color:var(--lime)">☏</span>+41 44 555 01 20</div>
      <div class="ct"><svg width="9" height="11" viewBox="0 0 9 11"><path d="M4.5 10S1 6.6 1 4.3a3.5 3.5 0 017 0C8 6.6 4.5 10 4.5 10z" fill="none" stroke="#b9ef3b"/><circle cx="4.5" cy="4.3" r="1.2" fill="#b9ef3b"/></svg><span>Seefeldgasse 12<br>8000 Zürich</span></div>
    </div>
    <div class="fbottom">© 2026 Druckfalter. Alle Rechte vorbehalten.<span><a>Impressum</a><a>Datenschutz</a><a>AGB</a></span></div>
  </footer>

</div>
</div>
</body>
</html>
```